Business Card

Just need business logo with phone number on it. 0487 312 654
And the following on the bottom of the card.

"Your local plumbing experts".
and emblems for zelpa card, cheque and cash

```html
<!DOCTYPE html>
<html lang="en">
<head>
<meta charset="utf-8">
<title>Redgum Plumbing &amp; Drainage – Business Card</title>
<link href="https://fonts.googleapis.com/css2?family=Exo+2:wght@400;700;800&display=swap" rel="stylesheet">
<style>
  :root {
    --backdrop: #9b9b9b;
    --brand-red: #ec1f2b;
    --brand-blue: #1a8fd0;
    --ink: #1d1d1d;
    --paper: #ffffff;
    --rule: #bdbdbd;
    --cash-black: #111111;
  }
  html, body {
    margin: 0;
    padding: 0;
    width: 1200px;
    height: 900px;
    overflow: hidden;
    background: var(--backdrop);
    font-family: "Exo 2", sans-serif;
  }
  .canvas { position: relative; width: 1200px; height: 900px; }

  .card {
    position: absolute;
    top: 306px;
    width: 440px;
    height: 272px;
    overflow: hidden;
  }
  .card--front { left: 149px; background: var(--paper); }
  .card--back { left: 609px; background: var(--brand-red); }

  .corner-mark { position: absolute; left: 0; top: 26px; }

  .phone {
    position: absolute;
    left: 44px;
    top: 35px;
    display: flex;
    align-items: center;
    gap: 6px;
    font-size: 17px;
    color: var(--ink);
  }

  .wordmark {
    position: absolute;
    font-weight: 800;
    text-transform: uppercase;
    line-height: 1;
    margin: 0;
  }
  .wordmark__name { display: block; letter-spacing: 1px; }
  .wordmark__trade { display: block; letter-spacing: 2.2px; margin-top: 4px; }

  .card--front .wordmark {
    right: 30px;
    top: 88px;
    text-align: right;
    color: var(--brand-red);
  }
  .card--front .wordmark__name { font-size: 34px; }
  .card--front .wordmark__trade { font-size: 12.5px; }

  .card--back .wordmark {
    left: 0;
    right: 0;
    top: 96px;
    text-align: center;
    color: var(--paper);
  }
  .card--back .wordmark__name { font-size: 46px; }
  .card--back .wordmark__trade { font-size: 16px; letter-spacing: 2.6px; }

  .tagline {
    position: absolute;
    left: 25px;
    top: 209px;
    margin: 0;
    font-size: 16px;
    color: var(--ink);
  }

  .payments {
    position: absolute;
    left: 241px;
    top: 198px;
    display: flex;
    gap: 9px;
    align-items: center;
  }
  .pay-card {
    height: 32px;
    box-sizing: border-box;
    display: flex;
    align-items: center;
    justify-content: center;
  }
  .pay-card--zelpa {
    width: 48px;
    background: var(--paper);
    border: 1px solid var(--rule);
    color: var(--ink);
    font-weight: 700;
    font-size: 13px;
  }
  .pay-card--cash { width: 46px; background: var(--cash-black); }

  .bottom-bands { position: absolute; left: 0; bottom: 0; }
</style>
</head>
<body>
<div class="canvas">

  <section class="card card--front" aria-label="Card front">
    <svg class="corner-mark" width="28" height="37" viewBox="0 0 28 37" aria-hidden="true">
      <polygon points="0,0 13,0 16,37 0,37" fill="var(--brand-red)"/>
      <polygon points="13,0 28,0 28,37 16,37" fill="var(--brand-blue)"/>
    </svg>

    <div class="phone">
      <svg width="24" height="24" viewBox="0 0 24 24" aria-hidden="true">
        <circle cx="12" cy="12" r="10.5" fill="none" stroke="var(--brand-red)" stroke-width="2"/>
        <path d="M7 10.5c0-2 2.2-3 5-3s5 1 5 3l-1.8.4-.5-1.6c-1.8-.6-3.6-.6-5.4 0l-.5 1.6z" fill="var(--brand-blue)"/>
        <rect x="8.5" y="11" width="7" height="5" rx="1" fill="var(--brand-blue)"/>
      </svg>
      <span>0487 312 654</span>
    </div>

    <h1 class="wordmark">
      <span class="wordmark__name">Redgum</span>
      <span class="wordmark__trade">Plumbing &amp; Drainage</span>
    </h1>

    <p class="tagline">Your local plumbing experts</p>

    <div class="payments" aria-label="Accepted payments">
      <div class="pay-card pay-card--zelpa">zelpa</div>
      <div class="pay-card pay-card--cash" aria-label="Cash">
        <svg width="18" height="18" viewBox="0 0 18 18" aria-hidden="true">
          <circle cx="9" cy="9" r="8.5" fill="var(--paper)"/>
          <text x="9" y="13.5" text-anchor="middle" font-family="Exo 2, sans-serif" font-weight="700" font-size="12" fill="var(--cash-black)">$</text>
        </svg>
      </div>
      <svg class="pay-card pay-card--cheque" width="60" height="32" viewBox="0 0 60 32" aria-label="Cheque">
        <rect x="4" y="5" width="54" height="25" fill="var(--paper)" stroke="#333" stroke-width="1.2"/>
        <rect x="1" y="2" width="54" height="25" fill="var(--paper)" stroke="#333" stroke-width="1.2"/>
        <line x1="6" y1="11" x2="48" y2="11" stroke="#555" stroke-width="1"/>
        <line x1="6" y1="16" x2="30" y2="16" stroke="#555" stroke-width="1"/>
        <rect x="36" y="14" width="14" height="5" fill="none" stroke="#555" stroke-width="1"/>
        <line x1="6" y1="22" x2="24" y2="22" stroke="#555" stroke-width="2"/>
      </svg>
    </div>

    <svg class="bottom-bands" width="440" height="21" viewBox="0 0 440 21" aria-hidden="true">
      <polygon points="0,6 217,6 209,21 0,21" fill="var(--brand-red)"/>
      <polygon points="222,0 440,0 440,21 207,21" fill="var(--brand-blue)"/>
    </svg>
  </section>

  <section class="card card--back" aria-label="Card back">
    <h2 class="wordmark">
      <span class="wordmark__name">Redgum</span>
      <span class="wordmark__trade">Plumbing &amp; Drainage</span>
    </h2>
  </section>

</div>
</body>
</html>
```